Quillmarsh Property Solutions need a business card design

Hello guys. We would need a business card design asap please.
We are a start up property investment business based in London UK specialised in buying, selling, managing and letting properties and helping distressed property owners.
The name of our Business is Quillmarsh, the logo symbolises the four fundamental elements of the world (earth, air, fire and water) and so it stands for strength, stability, longevity.
We would like the business card to communicate professionalism and reliability. Many many thanks indeed for your work.

Details:

1.) Rosalind Updike
Property Investor
Mobile: +44(0)7700123456
Email: rosalind.quillmarsh@mailbox-example.com

2.) Dominic Updike
Property Investor
Mobile: +44(0)7700987654
Email: dominic.quillmarsh@mailbox-example.com

```html
<!DOCTYPE html>
<html lang="en">
<head>
<meta charset="utf-8">
<title>Quillmarsh Property Solutions – Business Card</title>
<link rel="stylesheet" href="https://fonts.googleapis.com/css2?family=Open+Sans:wght@400;600;700&display=swap">
<style>
  :root {
    --backdrop: #e9e6e1;
    --card-white: #ffffff;
    --brand-grey: #8a8a8a;
    --text-dark: #3a3a3a;
    --accent-blue: #1f5fc8;
    --blue-light: #4f8ee6;
    --blue-mid: #3272d6;
    --blue-deep: #2158bd;
    --on-blue: #ffffff;
    --shadow: rgba(0, 0, 0, 0.18);
  }
  * { box-sizing: border-box; margin: 0; padding: 0; }
  html, body {
    width: 1200px;
    height: 720px;
    overflow: hidden;
    background: var(--backdrop);
    font-family: "Open Sans", Arial, sans-serif;
  }
  .canvas {
    position: relative;
    width: 1200px;
    height: 720px;
  }
  .card {
    position: absolute;
    width: 560px;
    height: 320px;
    box-shadow: 0 6px 18px var(--shadow);
  }

  /* Front: contact side */
  .card-front {
    left: 40px;
    top: 40px;
    background: var(--card-white);
  }
  .brand {
    position: absolute;
    left: 48px;
    top: 64px;
  }
  .brand-row {
    display: flex;
    align-items: center;
    gap: 10px;
  }
  .brand-mark {
    width: 18px;
    height: 18px;
    background: var(--brand-grey);
  }
  .brand-name {
    font-weight: 700;
    font-size: 26px;
    letter-spacing: 1px;
    color: var(--brand-grey);
  }
  .brand-tagline {
    margin-top: 2px;
    margin-left: 28px;
    font-size: 10px;
    font-weight: 600;
    letter-spacing: 1.5px;
    color: var(--brand-grey);
  }
  .contact {
    position: absolute;
    left: 48px;
    bottom: 44px;
    list-style: none;
    font-size: 14px;
    color: var(--text-dark);
  }
  .contact li {
    display: flex;
    align-items: center;
    gap: 8px;
    margin-top: 6px;
  }
  .contact svg { width: 14px; height: 14px; flex: none; }
  .person {
    position: absolute;
    right: 40px;
    top: 118px;
    text-align: right;
  }
  .person-name {
    font-size: 19px;
    font-weight: 700;
    color: var(--accent-blue);
  }
  .person-role {
    font-size: 12px;
    color: var(--text-dark);
    margin-top: 2px;
  }

  /* Back: brand side */
  .card-back {
    left: 600px;
    top: 360px;
    background: radial-gradient(circle at 40% 30%, var(--blue-light) 0%, var(--blue-mid) 45%, var(--blue-deep) 100%);
    display: flex;
    flex-direction: column;
    align-items: center;
    justify-content: center;
    gap: 26px;
  }
  .back-brand {
    display: flex;
    align-items: center;
    gap: 14px;
  }
  .back-mark {
    width: 26px;
    height: 26px;
    background: var(--on-blue);
  }
  .back-name {
    font-size: 40px;
    font-weight: 700;
    letter-spacing: 1.5px;
    color: var(--on-blue);
  }
  .web {
    font-size: 18px;
    letter-spacing: 2px;
    color: var(--on-blue);
  }
</style>
</head>
<body>
<main class="canvas">
  <section class="card card-front" aria-label="Business card front">
    <div class="brand">
      <div class="brand-row">
        <span class="brand-mark"></span>
        <span class="brand-name">QUILLMARSH</span>
      </div>
      <div class="brand-tagline">PROPERTY SOLUTIONS</div>
    </div>

    <div class="person">
      <div class="person-name">Rosalind Updike</div>
      <div class="person-role">Property Investor</div>
    </div>

    <ul class="contact">
      <li>
        <svg viewBox="0 0 14 14" aria-hidden="true">
          <rect x="3.5" y="0.5" width="7" height="13" rx="1.5" fill="var(--accent-blue)"/>
          <rect x="5" y="2.5" width="4" height="7" fill="var(--card-white)"/>
          <circle cx="7" cy="11.5" r="0.9" fill="var(--card-white)"/>
        </svg>
        <span>+44(0)7700123456</span>
      </li>
      <li>
        <svg viewBox="0 0 14 14" aria-hidden="true">
          <rect x="0.5" y="2.5" width="13" height="9" rx="1.5" fill="var(--accent-blue)"/>
          <path d="M1.5 3.5 L7 8 L12.5 3.5" fill="none" stroke="var(--card-white)" stroke-width="1.2"/>
        </svg>
        <span>rosalind.quillmarsh@mailbox-example.com</span>
      </li>
    </ul>
  </section>

  <section class="card card-back" aria-label="Business card back">
    <div class="back-brand">
      <span class="back-mark"></span>
      <span class="back-name">Quillmarsh</span>
    </div>
    <div class="web">www.quillmarsh-example.com</div>
  </section>
</main>
</body>
</html>
```